KTWG application splash screen

We need a 1024x768 image for use as an application splash screen.
The image will be displayed full screen on an 10 inch industrial PC 1024x768 screen while our application is launching. The image should convey that the application is "Waiting for connection to Wi-Fi access point..." and include a graphic of the industrial PC connected to the access point via an Ethernet cable. A list of troubleshooting steps should be included at the bottom of the image. The troubleshooting steps should not be the main focus of the image and should be shown in a smaller font (but still readable at 1024x768 displayed on a 10 inch screen).
I will include a mock up of the general idea of what we are looking for as well as image files for the industrial PC, a screenshot of our application to show on the PC's screen and the AP.
For general look and feel and a sense of corporate branding please review our website https://marrowgatesoilworks.example/. The splash screen should reflect corporate branding.
Target Market(s)
Users of our application
Industry/Entity Type
Agriculture
Look and feel

```html
<!DOCTYPE html>
<html lang="en">
<head>
<meta charset="utf-8">
<title>KTWG – Waiting for Wi-Fi access point</title>
<link rel="stylesheet" href="https://fonts.googleapis.com/css2?family=Poppins:wght@400;600;700&display=swap">
<style>
  :root {
    --sky-top: #27333f;
    --sky-mid: #4a5a63;
    --horizon: #6f7f5a;
    --field-mid: #3f5a24;
    --field-low: #2a3d17;
    --ink-light: #ffffff;
    --panel-bg: rgba(20, 24, 18, 0.86);
    --panel-line: #2c2f2a;
    --device-dark: #1d1f21;
    --device-edge: #3a3d40;
    --ap-white: #eef0f0;
  }
  * { margin: 0; padding: 0; box-sizing: border-box; }
  html, body { width: 1200px; height: 900px; overflow: hidden; background: #1a1f1a; }
  .splash {
    position: relative;
    width: 1200px; height: 900px;
    overflow: hidden;
    font-family: "Poppins", sans-serif;
    color: var(--ink-light);
  }
  .backdrop {
    position: absolute; inset: 0;
    background: linear-gradient(180deg, var(--sky-top) 0%, var(--sky-mid) 28%, #7d8a86 38%, var(--horizon) 41%, var(--field-mid) 58%, var(--field-low) 100%);
  }
  .headline {
    position: absolute; left: 0; right: 0; top: 54px;
    text-align: center;
    font-size: 45px; font-weight: 600; letter-spacing: -0.3px;
  }
  .pc-unit {
    position: absolute; left: 70px; top: 157px; width: 481px; height: 386px;
    border-radius: 22px;
    background: linear-gradient(180deg, var(--device-edge), var(--device-dark));
  }
  .ap-unit {
    position: absolute; left: 1044px; top: 127px; width: 38px; height: 307px;
    border-radius: 10px 10px 14px 14px;
    background: linear-gradient(90deg, #cfd3d3, var(--ap-white) 50%, #d4d8d8);
  }
  .cable { position: absolute; inset: 0; }
  .label {
    position: absolute; font-weight: 700; text-align: center; line-height: 1.0;
  }
  .label-pc { left: 152px; top: 557px; width: 300px; font-size: 20px; }
  .label-cable { left: 604px; top: 506px; width: 300px; font-size: 20px; }
  .label-ap { left: 932px; top: 541px; width: 260px; font-size: 20px; }
  .trouble {
    position: absolute; left: 19px; top: 675px; width: 1164px; height: 185px;
    background: var(--panel-bg);
    border: 2px solid var(--panel-line);
  }
  .trouble-title {
    position: absolute; left: 50px; top: 10px;
    font-size: 14.5px; font-weight: 700;
  }
  .trouble-rule {
    position: absolute; left: 0; right: 0; top: 42px; height: 2px; background: var(--panel-line);
  }
  .trouble-body {
    position: absolute; left: 60px; top: 50px; width: 840px;
    font-size: 12.8px; line-height: 20px; font-weight: 400;
  }
  .trouble-body ul { list-style: none; padding-left: 4px; }
  .trouble-body li::before { content: "•"; margin-right: 6px; }
  .brand {
    position: absolute; left: 930px; top: 62px; width: 190px; text-align: center;
  }
  .brand-name { font-size: 50px; font-weight: 700; line-height: 1; letter-spacing: 2px; }
  .brand-tag {
    margin-top: 6px; font-size: 12px; font-weight: 400;
    border-top: 1px solid var(--ink-light); padding-top: 3px;
  }
</style>
</head>
<body>
<main class="splash">
  <div class="backdrop" role="img" aria-label="Photo of a green soybean field under a cloudy evening sky"></div>

  <h1 class="headline">Waiting for connection to Wi-Fi access point...</h1>

  <svg class="cable" width="1200" height="900" viewBox="0 0 1200 900" aria-hidden="true">
    <path d="M551 480 H1045 Q1064 480 1064 461 V430" fill="none" stroke="var(--ink-light)" stroke-width="3"/>
  </svg>

  <div class="pc-unit" role="img" aria-label="Rugged tractor cab computer showing the seeding monitor application"></div>
  <div class="ap-unit" role="img" aria-label="White outdoor Wi-Fi access point with two antennas"></div>

  <div class="label label-pc">Tractor Cab Computer</div>
  <div class="label label-cable">Ethernet cable</div>
  <div class="label label-ap">WIFI Access Point<br>Relayon<br>RX-40 Outdoor</div>

  <section class="trouble">
    <h2 class="trouble-title">TROUBLESHOOTING STEPS:</h2>
    <div class="trouble-rule"></div>
    <div class="trouble-body">
      <p>This screen should only be visible for a short time on boot.</p>
      <p>If this screen stays visible for more than a minute:</p>
      <ul>
        <li>Verify that the Wi-Fi Access Point (AP) powers up when this system does (indicated by a green light on the side of the AP).</li>
        <li>Check the Ethernet cable between this system and the AP for damage, and replace it if necessary.</li>
        <li>Power-cycle this system and wait for it to reboot fully.</li>
        <li>If the issue persists, contact KTWG support for further assistance.</li>
      </ul>
    </div>
    <div class="brand">
      <div class="brand-name">KTWG</div>
      <div class="brand-tag">Marrowgate Soil Works Inc.</div>
    </div>
  </section>
</main>
</body>
</html>
```